New web design for a service provider in the medical field

We are looking for a new design for our website. We are a company that repairs and sells medical endoscopes. Our customers include doctors and hospitals. Our current website can be found at https://lumavex.de/en/lumavex-english.
We need a new web design (without programming) for the following 3 pages:
-Startpage https://lumavex.de/en/lumavex-english/
-Used endoscopes https://lumavex.de/en/used-endoscopes/
-Purchase https://lumavex.de/en/purchase/
The design should be modern and stylish.
The blue color of the logo should be reflected on the page, but not too intrusive.
I have uploaded the images from the header. If more images are needed, let me know and I will upload them.

Target Market(s)
Doctors and hospitals

```html
<!DOCTYPE html>
<html lang="en">
<head>
<meta charset="utf-8">
<title>Lumavex – Endoscope Service</title>
<link rel="stylesheet" href="https://fonts.googleapis.com/css2?family=Poppins:wght@300;400;500;600;700&display=swap">
<style>
:root{
  --blue:#27a4de;
  --blue-dark:#1a8fc9;
  --ink:#1b1f24;
  --muted:#555c63;
  --navy:#2c4a64;
  --navy-soft:#3b5b78;
  --tint:#eef7fc;
  --card:#f7f9fb;
  --line:#bfe2f4;
  --stage:#f1f3f5;
}
*{box-sizing:border-box;margin:0;padding:0}
html,body{width:1152px;height:1200px;overflow:hidden;background:var(--stage);font-family:"Poppins",sans-serif;color:var(--ink)}
.stage{position:absolute;left:0;top:0;width:1882px;height:1960px;transform:scale(.6121);transform-origin:0 0}
.page{position:absolute;background:#fff;box-shadow:0 10px 40px rgba(20,40,60,.18);overflow:hidden}
.page--home{left:243px;top:127px;width:636px;height:1706px}
.page--detail{left:1023px;top:122px;width:618px;height:1704px}
.abs{position:absolute}
.center{text-align:center}
.blue{color:var(--blue)}

/* top bar */
.topbar{left:0;top:0;width:636px;height:31px;background:var(--blue);color:#fff;font-size:7px}
.topbar__claim{left:45px;top:11px}
.topbar__contact{right:96px;top:11px;display:flex;gap:8px}
.topbar__lang{right:40px;top:0;width:44px;height:31px;background:#4bb6e6;font-size:6px;font-weight:600;display:flex;align-items:center;justify-content:center}
/* nav */
.nav{left:0;top:31px;width:636px;height:65px;border-bottom:1px solid #eee}
.brand{left:45px;top:22px;display:flex;align-items:center;gap:6px;font-size:12px;font-weight:600;color:var(--navy)}
.brand__dot{width:10px;height:10px;border-radius:50%;background:var(--blue)}
.nav__menu{left:149px;top:28px;display:flex;gap:12px;font-size:8px;font-weight:500}
.nav__menu .is-active{color:var(--blue)}
/* hero */
.hero{left:0;top:96px;width:636px;height:266px;background:linear-gradient(100deg,#c9dde9 0%,#a9cbe0 45%,#8dbcd8 100%)}
.hero__pre,.hero__main,.hero__sub{line-height:1;width:100%;color:#fff}
.hero__pre{top:37px;font-size:25px;font-weight:300;letter-spacing:8px}
.hero__main{top:72px;font-size:50px;font-weight:700}
.hero__sub{top:137px;font-size:34px;font-weight:700}
.hero__rule{left:235px;top:177px;width:166px;height:2px;background:#fff}
.btn{display:flex;align-items:center;justify-content:center;border-radius:3px;font-weight:400}
.btn--solid{background:var(--blue);color:#fff}
.btn--outline{border:1px solid var(--blue);color:var(--blue);background:#fff;font-size:10px}
.hero__btn{left:244px;top:198px;width:148px;height:36px;font-size:14px}
/* intro */
.h2{font-size:17px;font-weight:500}
.intro__title{top:494px;width:100%}
.intro__text{top:528px;left:100px;width:436px;font-size:10px;line-height:21.5px}
/* feature box */
.feature{left:43px;top:720px;width:554px;height:261px}
.feature__text{left:0;top:0;width:285px;height:261px;background:var(--blue);color:#fff;padding:22px 18px}
.feature__title{font-size:14px;line-height:20px}
.feature__claim{font-size:12px;margin-top:4px}
.feature__body{font-size:8.5px;line-height:13px;margin-top:18px}
.feature__body p+p{margin-top:13px}
.feature__photo{left:285px;top:0;width:269px;height:261px;background:linear-gradient(135deg,#e8edf1,#b9c2c9 60%,#5b6168)}
/* second hand */
.second__kicker{top:1061px;width:100%;font-size:12px}
.second__title{top:1085px;width:100%}
.model{top:1138px;width:178px;height:166px}
.model__photo{left:0;top:0;width:178px;height:166px}
.model__label{left:0;bottom:0;width:178px;height:36px;background:linear-gradient(0deg,#fff 70%,rgba(255,255,255,.6));display:flex;align-items:center;justify-content:space-between;padding:0 14px 0 22px;font-size:14px;font-weight:500}
.chev{width:17px;height:17px;border-radius:50%;background:var(--blue);display:flex;align-items:center;justify-content:center}
/* services */
.service{top:1385px;width:187px}
.service__icon{margin:0 auto;width:50px;height:50px;border-radius:50%;background:var(--blue);display:flex;align-items:center;justify-content:center}
.service__title{margin-top:18px;font-size:18px;font-weight:600;color:var(--blue)}
.service__sub{margin-top:10px;font-size:12px;font-weight:500}
.service__text{margin-top:12px;font-size:8.5px;line-height:16px;color:var(--muted);height:108px}
.service__btn{margin:0 auto;width:131px;height:33px}
.divider{top:1385px;width:1px;height:272px;background:#e6e9ec}

/* detail page */
.stub{top:-12px;width:126px;height:26px}
.banner{left:0;top:90px;width:618px;height:205px;background:linear-gradient(110deg,#2a6fd0 0%,#3aa0e8 45%,#1b4fb0 100%);color:#fff}
.banner__title{top:50px;width:100%;font-size:15px;font-weight:500}
.banner__sub{top:75px;width:100%;font-size:9px;font-weight:500}
.banner__cta{top:91px;width:100%;font-size:16px;font-weight:500}
.banner__btn{left:246px;top:126px;width:126px;height:30px;background:#fff;color:var(--blue);font-size:9.5px}
.outcome__title{top:376px;width:100%;font-size:16px;font-weight:600}
.value{width:173px;background:var(--card);border-radius:3px;padding:22px 12px 0}
.value__title{font-size:13px;line-height:17px;font-weight:400}
.value__text{font-size:8px;line-height:14px;margin-top:14px}
.decision__title{top:740px;width:100%;font-size:16px;line-height:27px;font-weight:400}
.perk{width:168px}
.perk__head{height:86px;background:var(--tint);display:flex;align-items:center;gap:12px;padding:0 10px}
.perk__icon{flex:none;width:32px;height:32px;border-radius:50%;background:#fff;display:flex;align-items:center;justify-content:center}
.perk__name{font-size:11px;line-height:17px;font-weight:500}
.perk__body{height:151px;border:1px solid var(--line);border-top:none;border-radius:0 0 3px 3px;padding:28px 12px 0;font-size:8px;line-height:14.6px;text-align:center}
.help{left:0;top:1399px;width:618px;height:198px;background:var(--navy);color:#fff}
.help__title{left:90px;top:54px;font-size:16px;font-weight:600;letter-spacing:.3px}
.help__sub{left:92px;top:82px;font-size:9px}
.help__btn{left:108px;top:115px;width:143px;height:34px;font-size:13px}
.help__figure{left:372px;top:0;width:168px;height:198px;background:linear-gradient(180deg,var(--navy-soft) 0%,var(--navy) 100%)}
.footer{left:0;top:1600px;width:618px;height:104px;background:var(--blue);color:#fff}
.footer__links{top:32px;width:100%;display:flex;justify-content:center;gap:24px;font-size:7.5px;font-weight:500}
.footer__rule{left:44px;top:66px;width:531px;height:1px;background:rgba(255,255,255,.55)}
.footer__copy{top:81px;width:100%;font-size:7.5px}
</style>
</head>
<body>
<div class="stage">

  <!-- Start page -->
  <section class="page page--home">
    <div class="abs topbar">
      <span class="abs topbar__claim">Cause the outcome matters</span>
      <span class="abs topbar__contact"><span>✉ info@lumavex.de</span><span>|</span><span>☎ +49 4100 555 010-0</span><span>|</span><span>About us</span><span>|</span><span>Contact us</span></span>
      <span class="abs topbar__lang">ENGLISH</span>
    </div>
    <header class="abs nav">
      <div class="abs brand"><span class="brand__dot"></span>Lumavex</div>
      <nav class="abs nav__menu"><span class="is-active">Home</span><span>Endoscope Repair</span><span>Used Endoscopes</span><span>Endoscopy Systems</span><span>Endoscopy Accessories</span><span>Purchase</span></nav>
    </header>
    <div class="abs hero" role="img" aria-label="Photo of endoscope control bodies in a clinic, tinted light blue">
      <div class="abs hero__pre center">PUT YOUR</div>
      <div class="abs hero__main center">ENDOSCOPE</div>
      <div class="abs hero__sub center">IN RELIABLE HANDS!</div>
      <div class="abs hero__rule"></div>
      <div class="abs btn btn--solid hero__btn">Pick-up order</div>
    </div>

    <h2 class="abs h2 intro__title center">YOUR FUTURE – <span class="blue">OUR SERVICE</span></h2>
    <p class="abs intro__text center">Lumavex GmbH is specialised in the repair and sale of Orvian, Pentrel and Fujora flexible medical endoscopes. As a service-oriented company, we are at your side with our knowledge and skills!</p>

    <div class="abs feature">
      <div class="abs feature__text center">
        <div class="feature__title">Endoscope repairs &amp; second hand endoscopes from Lumavex</div>
        <div class="feature__claim">cause the outcome matters!</div>
        <div class="feature__body">
          <p>Lumavex is a privileged partner for the start-up facility or optimisation of existing healthcare facilities, doctor's offices and hospitals. The quality and reliability of our products and our offered service are our best advertisement!</p>
          <p>As a result of optimised processes and highly qualified specialists in our company, we can work very quickly and with high quality for your benefit of least possible restrictions in your doctor's office or in your hospital.</p>
        </div>
      </div>
      <div class="abs feature__photo" role="img" aria-label="Close-up photo of an endoscope control head"></div>
    </div>

    <div class="abs second__kicker center blue">Second Hand</div>
    <h2 class="abs h2 second__title center">Orvian , Pentrel, Fujora Endoscopes</h2>

    <div class="abs model" style="left:43px">
      <div class="abs model__photo" role="img" aria-label="Photo of a technician holding an endoscope" style="background:linear-gradient(160deg,#e9eef3,#b7c7d8)"></div>
      <div class="abs model__label">Orvian<span class="chev"><svg width="7" height="7" viewBox="0 0 7 7"><path d="M2 1l3 2.5L2 6" fill="none" stroke="#fff" stroke-width="1.3"/></svg></span></div>
    </div>
    <div class="abs model" style="left:229px">
      <div class="abs model__photo" role="img" aria-label="Photo of an endoscope control body" style="background:linear-gradient(160deg,#d7dbe0,#3b4046)"></div>
      <div class="abs model__label">Pentrel<span class="chev"><svg width="7" height="7" viewBox="0 0 7 7"><path d="M2 1l3 2.5L2 6" fill="none" stroke="#fff" stroke-width="1.3"/></svg></span></div>
    </div>
    <div class="abs model" style="left:416px">
      <div class="abs model__photo" role="img" aria-label="Photo of gloved hands inspecting an endoscope" style="background:linear-gradient(160deg,#dfe6f3,#b9a9e0)"></div>
      <div class="abs model__label">Fujora<span class="chev"><svg width="7" height="7" viewBox="0 0 7 7"><path d="M2 1l3 2.5L2 6" fill="none" stroke="#fff" stroke-width="1.3"/></svg></span></div>
    </div>

    <div class="abs divider" style="left:225px"></div>
    <div class="abs divider" style="left:412px"></div>

    <div class="abs service center" style="left:38px">
      <div class="service__icon"><svg width="26" height="26" viewBox="0 0 26 26" fill="none" stroke="#fff" stroke-width="2"><circle cx="13" cy="9" r="5"/><path d="M4 24c1-6 5-8 9-8s8 2 9 8"/></svg></div>
      <div class="service__title">Repair</div>
      <div class="service__sub">Endoscope repair service</div>
      <p class="service__text">Manufacturer-independent we repair and maintain endoscopes, individual components (e.g. processors or light sources), accessories and peripherals of the manufacturers Orvian, Pentrel and Fujora.</p>
      <div class="btn btn--outline service__btn">Repaire Request</div>
    </div>
    <div class="abs service center" style="left:225px">
      <div class="service__icon"><svg width="26" height="26" viewBox="0 0 26 26" fill="none" stroke="#fff" stroke-width="2"><circle cx="13" cy="15" r="7"/><path d="M13 11v8M11 13h3.5a1.5 1.5 0 010 3H11M4 6l5 3M22 6l-5 3"/></svg></div>
      <div class="service__title">Sale</div>
      <div class="service__sub">Used endoscopes</div>
      <p class="service__text">Our regular stock includes refurbished gastroscopes, colposcopes, bronchoscopes, cystoscopes and duodenoscopes from the well-known manufacturers Orvian, Pentrel and Fujora.</p>
      <div class="btn btn--outline service__btn">Purchase Request</div>
    </div>
    <div class="abs service center" style="left:412px">
      <div class="service__icon"><svg width="26" height="26" viewBox="0 0 26 26" fill="none" stroke="#fff" stroke-width="2"><path d="M4 9l9-5 9 5v9l-9 5-9-5z"/><path d="M4 9l9 5 9-5M13 14v9"/></svg></div>
      <div class="service__title">Purchase</div>
      <div class="service__sub">Used endoscopes</div>
      <p class="service__text">We are very interested in buying your old endoscopes – even defective and dismantled! We offer fair conditions! Please contact us for a purchase offer!</p>
      <div class="btn btn--outline service__btn">Sell Device</div>
    </div>
  </section>

  <!-- Detail page -->
  <section class="page page--detail">
    <div class="abs btn btn--outline stub" style="left:66px">Repaire Request</div>
    <div class="abs btn btn--outline stub" style="left:246px">Purchase Request</div>
    <div class="abs btn btn--outline stub" style="left:426px">Sell Device</div>

    <div class="abs banner" role="img" aria-label="Blue abstract medical imagery with a glowing network pattern">
      <div class="abs banner__title center">FAULTY ENDOSCOPE?</div>
      <div class="abs banner__sub center">We ensure quick and smooth repairs!</div>
      <div class="abs banner__cta center">Simple place a</div>
      <div class="abs btn banner__btn">Pick-up Order</div>
    </div>

    <h2 class="abs outcome__title center"><span class="blue">CAUSE</span> THE OUTCOME MATTERS!</h2>

    <div class="abs value center" style="left:44px;top:418px;height:119px"><div class="value__title">One Company For EveryOne</div><p class="value__text">We are a service provider for doctors and hospitals!</p></div>
    <div class="abs value center" style="left:223px;top:418px;height:119px"><div class="value__title">Experiences Characterises Us</div><p class="value__text">Our team has many years of experience in the business field!</p></div>
    <div class="abs value center" style="left:401px;top:418px;height:119px"><div class="value__title">The Product is Close to Our Heart</div><p class="value__text">We repair and sell second hand, flexible endoscopes!</p></div>
    <div class="abs value center" style="left:44px;top:542px;height:120px"><div class="value__title">Guaranteed Service</div><p class="value__text" style="margin-top:24px">You receive a six-month warranty on all repairs!</p></div>
    <div class="abs value center" style="left:223px;top:542px;height:120px"><div class="value__title">Quality not Quantity</div><p class="value__text" style="margin-top:24px">Reliability and durability instead of inferior replacements!</p></div>
    <div class="abs value center" style="left:401px;top:542px;height:120px"><div class="value__title">Services for EveryOne</div><p class="value__text" style="margin-top:24px">Our service includes the manufacturers Orvian, Pentrel and Fujora!</p></div>

    <h2 class="abs decision__title center"><span class="blue" style="font-weight:600">Lumavex GmbH,</span><br>your decision for your future</h2>

    <div class="abs perk" style="left:44px;top:832px">
      <div class="perk__head"><span class="perk__icon"><svg width="18" height="18" viewBox="0 0 18 18" fill="none" stroke="#27a4de" stroke-width="1.6"><circle cx="10" cy="10" r="6"/><path d="M10 6v4l3 2M1 8h4M2 12h3"/></svg></span><span class="perk__name">Fast repairs</span></div>
      <p class="perk__body">Keep potential disruptions in your doctor's office or in your hospital at minimum as a result of optimized processes and highly qualified specialists in our company</p>
    </div>
    <div class="abs perk" style="left:226px;top:832px">
      <div class="perk__head"><span class="perk__icon"><svg width="18" height="18" viewBox="0 0 18 18" fill="none" stroke="#27a4de" stroke-width="1.6"><path d="M2 16V11M6 16V7M10 16V10"/><circle cx="13.5" cy="12" r="3.5"/><path d="M5 4l3-3 3 3"/></svg></span><span class="perk__name">Highly cost<br>efficient</span></div>
      <p class="perk__body">Benefit from our first class recommendations and implementation by our experienced staff. Our goals is to find the best solutions together with you at the best lowest price point.</p>
    </div>
    <div class="abs perk" style="left:407px;top:832px">
      <div class="perk__head"><span class="perk__icon"><svg width="18" height="18" viewBox="0 0 18 18" fill="none" stroke="#27a4de" stroke-width="1.6"><path d="M2 9l7-6 7 6M4 8v8h10V8"/><path d="M7 16v-4h4v4"/></svg></span><span class="perk__name">On-site service</span></div>
      <p class="perk__body">We will gladly pay you a visit to to carry out analysis and repairs on site. Due to our many years of experience – it doesn't get any faster (whigleithin a 250 km range)</p>
    </div>
    <div class="abs perk" style="left:44px;top:1084px">
      <div class="perk__head"><span class="perk__icon"><svg width="18" height="18" viewBox="0 0 18 18" fill="none" stroke="#27a4de" stroke-width="1.6"><rect x="5" y="2" width="8" height="14" rx="2"/><path d="M8 13h2"/></svg></span><span class="perk__name">Loan equipment<br>service</span></div>
      <p class="perk__body">Use our service of high-quality loan devices during the downtime of your defective endoscope (limited to stock)</p>
    </div>
    <div class="abs perk" style="left:226px;top:1084px">
      <div class="perk__head"><span class="perk__icon"><svg width="18" height="18" viewBox="0 0 18 18" fill="none" stroke="#27a4de" stroke-width="1.6"><path d="M15 9a6 6 0 11-2-4.5"/><path d="M15 2v3h-3"/><path d="M7 11l4-4"/></svg></span><span class="perk__name">Without a<br>maintenance<br>contract</span></div>
      <p class="perk__body">No subscription or other maintenance contract, but one-time and sustainable repair work</p>
    </div>
    <div class="abs perk" style="left:407px;top:1084px">
      <div class="perk__head"><span class="perk__icon"><svg width="18" height="18" viewBox="0 0 18 18" fill="none" stroke="#27a4de" stroke-width="1.6"><path d="M3 10a6 6 0 0112 0"/><rect x="2" y="10" width="3" height="4" rx="1"/><rect x="13" y="10" width="3" height="4" rx="1"/></svg></span><span class="perk__name">First class service</span></div>
      <p class="perk__body">Our clients always come first!</p>
    </div>

    <div class="abs help">
      <div class="abs help__title">HOW CAN WE HELP YOU?</div>
      <div class="abs help__sub">Send us a Message We will Contact You</div>
      <div class="abs btn btn--solid help__btn">Send Message</div>
      <div class="abs help__figure" role="img" aria-label="Illustration of a support agent holding a phone"></div>
    </div>

    <footer class="abs footer">
      <nav class="abs footer__links"><span>INFORMATIONS</span><span>ABOUT US</span><span>CONTACT US</span><span>TOS</span><span>COPYRIGHTS</span><span>PRIVACY POLICY</span></nav>
      <div class="abs footer__rule"></div>
      <div class="abs footer__copy center">© 2022 Lumavex GmbH</div>
    </footer>
  </section>

</div>
</body>
</html>
```